One business card required with 2 company logos and 2 people's details

One business card required.
No preference on design - One side could show the 2 different business logos for the companies we own. The reverse could have the details shown below.
Another option could be one business one side and one business on the reverse. Happy to receive designs.

Dora Pellham
07700 913 286
Rowena Tindall
07700 958 137

website: quietmeadowbloom.co.uk
email: info@quietmeadowbloom.co.uk

website: brightharbourevents.co.uk
email: info:brightharbourevents.co.uk

May be nice to have icons instead of the words email/website?

I have included different versions of the logos to help with your design.

Contact Information for Business Card

see project overview

Requirements
Must have
• both company logos, both contact names and contact details

```html
<!DOCTYPE html>
<html lang="en">
<head>
<meta charset="utf-8">
<title>Bright Harbour Events &amp; Quiet Meadow Bloom – Business Card</title>
<link rel="stylesheet" href="https://fonts.googleapis.com/css2?family=Raleway:wght@700&family=Arimo:wght@400&display=swap">
<style>
  :root {
    --page-bg: #2b2d31;
    --card-black: #030405;
    --navy: #0d1a24;
    --navy-light: #1b2a35;
    --white: #ffffff;
    --ink: #15202a;
    --blue: #1f6fe0;
    --teal: #2ec4d6;
    --brand-blue: #1e8cf0;
    --brand-violet: #4a4a78;
  }
  * { box-sizing: border-box; margin: 0; padding: 0; }
  html, body {
    width: 1200px; height: 900px; overflow: hidden;
    background: var(--page-bg);
  }
  .card {
    position: absolute; left: 250px; width: 700px; height: 400px;
    overflow: hidden; box-shadow: 0 8px 24px rgba(0,0,0,.45);
  }
  /* Front */
  .card--front { top: 35px; background: var(--card-black); display: flex; align-items: center; justify-content: center; }
  .front-brand {
    font-family: "Raleway", sans-serif; font-weight: 700;
    font-size: 40px; letter-spacing: 2px; color: var(--brand-blue);
    text-transform: uppercase;
  }
  /* Back */
  .card--back { top: 465px; background: var(--white); }
  .back-panel { position: absolute; inset: 0; }
  .name-band {
    position: absolute; height: 40px; padding-left: 26px;
    display: flex; align-items: center;
    background: linear-gradient(90deg, var(--blue), var(--teal));
    font-family: "Raleway", sans-serif; font-weight: 700; font-size: 25px; color: var(--white);
  }
  .name-band--first { left: 14px; top: 44px; width: 236px; }
  .name-band--second { left: 26px; top: 122px; width: 300px; }
  .phone-row {
    position: absolute; display: flex; align-items: center; gap: 20px;
    font-family: "Arimo", sans-serif; font-size: 18px;
  }
  .phone-row--first { left: 40px; top: 88px; color: var(--ink); }
  .phone-row--second { left: 52px; top: 170px; color: var(--white); }
  .phone-row svg { width: 18px; height: 18px; }
  .contact-list {
    position: absolute; left: 74px; bottom: 26px;
    display: grid; grid-template-columns: 28px auto; column-gap: 16px;
    font-family: "Arimo", sans-serif; font-size: 17px; line-height: 20px; color: var(--white);
  }
  .contact-icon { grid-row: span 2; align-self: center; width: 20px; height: 20px; }
  .glow-line {
    position: absolute; left: 110px; right: 40px; bottom: 10px; height: 3px;
    background: linear-gradient(90deg, transparent, var(--teal) 40%, var(--teal) 70%, transparent);
    box-shadow: 0 0 8px var(--teal);
  }
  .logo-badge {
    position: absolute; left: 440px; top: 55px; width: 240px; height: 240px;
    border-radius: 50%; background: var(--white);
    display: flex; align-items: center; justify-content: center; text-align: center;
    font-family: "Raleway", sans-serif; font-weight: 700; font-size: 30px; line-height: 1.15;
    color: var(--brand-violet);
  }
</style>
</head>
<body>

<section class="card card--front">
  <p class="front-brand">Bright Harbour Events</p>
</section>

<section class="card card--back">
  <svg class="back-panel" viewBox="0 0 700 400" aria-hidden="true">
    <defs>
      <linearGradient id="navyFade" x1="0" y1="0" x2="1" y2="1">
        <stop offset="0" stop-color="#0a141c"/>
        <stop offset="1" stop-color="#25343f"/>
      </linearGradient>
      <linearGradient id="ringArc" x1="0" x2="1">
        <stop offset="0" stop-color="#2ec4d6"/>
        <stop offset="1" stop-color="#6a4fd0"/>
      </linearGradient>
    </defs>
    <polygon points="0,175 470,110 700,110 700,400 0,400" fill="url(#navyFade)"/>
    <path d="M455 210 A115 115 0 0 0 665 210" fill="none" stroke="url(#ringArc)" stroke-width="2" transform="translate(0,-5)"/>
  </svg>

  <div class="logo-badge">Quiet Meadow<br>Bloom</div>

  <div class="name-band name-band--first">Dora Pellham</div>
  <div class="phone-row phone-row--first">
    <svg viewBox="0 0 24 24"><path fill="#2ec4d6" d="M6.6 10.8a15 15 0 0 0 6.6 6.6l2.2-2.2c.3-.3.7-.4 1-.2 1.1.4 2.3.6 3.6.6.6 0 1 .4 1 1V20c0 .6-.4 1-1 1A17 17 0 0 1 3 4c0-.6.4-1 1-1h3.5c.6 0 1 .4 1 1 0 1.3.2 2.5.6 3.6.1.3 0 .7-.2 1z"/></svg>
    <span>07700 913 286</span>
  </div>

  <div class="name-band name-band--second">Rowena Tindall</div>
  <div class="phone-row phone-row--second">
    <svg viewBox="0 0 24 24"><path fill="#2ec4d6" d="M6.6 10.8a15 15 0 0 0 6.6 6.6l2.2-2.2c.3-.3.7-.4 1-.2 1.1.4 2.3.6 3.6.6.6 0 1 .4 1 1V20c0 .6-.4 1-1 1A17 17 0 0 1 3 4c0-.6.4-1 1-1h3.5c.6 0 1 .4 1 1 0 1.3.2 2.5.6 3.6.1.3 0 .7-.2 1z"/></svg>
    <span>07700 958 137</span>
  </div>

  <div class="contact-list">
    <svg class="contact-icon" viewBox="0 0 24 24"><rect x="2" y="5" width="20" height="14" fill="#2ec4d6"/><path d="M2 5l10 8 10-8" fill="none" stroke="#0d1a24" stroke-width="1.6"/></svg>
    <span>info:brightharbourevents.co.uk</span>
    <span>info@quietmeadowbloom.co.uk</span>
    <svg class="contact-icon" viewBox="0 0 24 24" fill="none" stroke="#2ec4d6" stroke-width="1.8"><circle cx="12" cy="12" r="9"/><ellipse cx="12" cy="12" rx="4" ry="9"/><path d="M3 12h18M5 7h14M5 17h14"/></svg>
    <span>www.brightharbourevents.co.uk</span>
    <span>www.quietmeadowbloom.co.uk</span>
  </div>

  <div class="glow-line"></div>
</section>

</body>
</html>
```